kolvarin.link kolvarin.space kolvarin.press website

The website is named KOLVARIN and it will have 3 domain names. kolvarin.link, press, space.
I'd like it to be viewed on Pads, pcs and phones.

page menu:

kolvarin.link(start page): presentation of company. (creative, design, app, new product innovation.)
Here we'll need sosial media icons: plimber, vendoloop, mirtavel, trelvanet. (light but some 'fruity' colors)

kolvarin.press: blog. It will be a 75% picture blog > rest will be text. I need to be able to resize pictures and shape columns to picture size. (light but some 'fruity' colors)

kolvarin.space : the fun part of this web design, however, on entering the page I'd like a non-disclosure agreement where viewer simply click "yes, I agree" after filling out contact info. (check attached document)
We will have space here for uploading PDF files viewers can download. There is also a blog space here to tell in brief about the PDF file. (maybe a space/sci-fi theme her e.g spacechimp, Laika the space dog?)

I will attach the logo here I want you to use > and develop for the .space .press webpage. The logo i uploaded is for the .link page.

Target Market(s)

venture capitalists

Number of Pages Required

3 page

Requirements
Must have
• a few 'fruity colors' but mostly white and grey

```html
<!DOCTYPE html>
<html lang="en">
<head>
<meta charset="utf-8">
<title>Kolvarin Link</title>
<link href="https://fonts.googleapis.com/css2?family=Lato:wght@400;700&family=Signika:wght@700&family=Maven+Pro:wght@400;500&family=Great+Vibes&display=swap" rel="stylesheet">
<style>
:root{
  --ink:#1c1c1c;
  --header-bg:#f8f8f8;
  --cream:#fdf8f0;
  --red:#e2352b;
  --orange:#f07d1a;
  --yellow:#f2dc1a;
  --green:#5f9a3c;
  --green-dark:#3f7428;
  --blue:#3b5998;
  --sky:#2ba7e0;
  --teal:#1e7bb5;
  --slate:#6c7a89;
}
*{box-sizing:border-box;margin:0;padding:0}
html,body{width:946px;height:1200px;overflow:hidden}
body{position:relative;font-family:'Lato',sans-serif;color:var(--ink);background:#fff}
.abs{position:absolute}

.site-header{position:absolute;left:0;top:0;width:946px;height:108px;background:var(--header-bg)}
.brand{position:absolute;left:78px;top:34px;display:flex;align-items:center;gap:8px}
.brand-mark{width:20px;height:20px;background:var(--orange)}
.brand-name{font-family:'Lato',sans-serif;font-weight:700;font-size:24px;letter-spacing:1px;color:var(--ink)}
.social{display:flex;gap:4px}
.social span{display:block;height:22px;padding:0 3px;border-radius:3px;color:#fff;font:700 7px/22px 'Lato',sans-serif}
.header-social{position:absolute;right:78px;top:18px}
.s1{background:var(--blue)}.s2{background:var(--sky)}.s3{background:var(--teal)}.s4{background:var(--slate)}
.contact-line{position:absolute;top:66px;display:flex;align-items:center;gap:8px;font-size:14px;color:var(--ink)}
.menu-toggle{position:absolute;left:831px;top:62px;width:37px;height:27px;border:1px solid #ccc;background:#fff}
.menu-toggle i{position:absolute;left:7px;width:22px;height:2px;background:#222}

.hero{position:absolute;left:0;top:108px;width:946px;height:372px;
  background:radial-gradient(ellipse at 50% 45%,#fafafa 0%,#e6e6e6 55%,#d5d5d5 100%)}
.hero-floor{position:absolute;left:0;top:287px;width:946px;height:85px;background:linear-gradient(#e9e9e9,#dedede)}
.lamps{position:absolute;left:400px;top:0;width:145px;height:72px;background:linear-gradient(#d9d9d9,#ececec);border-radius:0 0 8px 8px}
.hero-title{position:absolute;left:0;top:100px;width:946px;text-align:center;font-family:'Signika',sans-serif;font-weight:700;font-size:28px;color:#333;letter-spacing:.5px;text-shadow:0 2px 3px rgba(0,0,0,.2)}
.devices{position:absolute;left:165px;top:157px;width:590px;height:292px;border-radius:8px;
  background:linear-gradient(100deg,#3a3a3a 0%,#f0a040 25%,#ffffff 50%,#f08a2a 75%,#3a3a3a 100%);opacity:.85}
.btn-contact{position:absolute;left:419px;top:157px;width:108px;height:32px;background:var(--red);color:#fff;border-radius:2px;
  font:700 14px/32px 'Lato',sans-serif;text-align:center}
.dots{position:absolute;left:448px;top:341px;display:flex;gap:6px}
.dots span{width:12px;height:12px;border-radius:50%;border:1px solid #bbb;background:#fff}
.dots .on{background:var(--red);box-shadow:inset 0 0 0 2px #fff;border-color:#333}

.services{position:absolute;left:0;top:480px;width:946px;height:340px;background:var(--cream)}
.card{position:absolute;top:50px;width:250px}
.card-media{height:152px;border-top:3px solid}
.card h3{margin-top:30px;margin-left:2px;font-family:'Maven Pro',sans-serif;font-weight:400;font-size:18px;color:#222}
.card p{margin:7px 2px 0;font-size:10.5px;line-height:15px;color:#333}

.about{position:absolute;left:0;top:848px;width:946px;text-align:center}
.about h2{font-family:'Maven Pro',sans-serif;font-weight:500;font-size:22px;line-height:30px}
.about h2 .a{color:var(--orange)} .about h2 .c{color:var(--yellow)}
.divider{position:relative;margin:6px auto 0;width:250px;height:20px}
.divider:before{content:"";position:absolute;left:0;right:0;top:14px;height:1px;background:#f1e2d0}
.divider i{position:absolute;left:118px;top:3px;width:15px;height:18px;border-radius:50%;background:var(--orange)}
.about p{margin:16px auto 0;width:730px;font-size:11.5px;line-height:19.5px;color:#222}

.newsletter-band{position:absolute;left:0;top:1048px;width:946px;height:61px;background:var(--green);border-top:3px solid var(--green-dark)}
.signup{position:absolute;left:107px;top:19px;display:flex}
.signup input{width:233px;height:22px;border:1px solid #ddd;padding-left:7px;font:10px 'Lato',sans-serif;color:#333}
.signup button{width:28px;height:22px;border:0;background:var(--red);color:#fff;font:700 10px 'Lato',sans-serif}
.footer-brand{position:absolute;left:470px;top:18px;display:flex;align-items:center;gap:6px}
.footer-brand .brand-name{font-size:18px;color:#fff}
.footer-brand .brand-mark{width:14px;height:14px;background:var(--yellow)}
.follow-group{position:absolute;right:78px;top:16px;display:flex;align-items:center;gap:10px}
.follow{font-family:'Great Vibes',cursive;font-size:19px;color:#fff;white-space:nowrap}

.info-band{position:absolute;left:0;top:1109px;width:946px;height:91px;background:linear-gradient(#2f2f2f,#404040)}
.info-row{position:absolute;top:17px;display:flex;align-items:center;gap:7px;font-size:10px;color:#fff}
.copyright{position:absolute;left:0;top:60px;width:946px;text-align:center;font-size:9.5px;color:#fff}
</style>
</head>
<body>

<header class="site-header">
  <div class="brand"><span class="brand-mark"></span><span class="brand-name">KOLVARIN</span></div>
  <nav class="social header-social">
    <span class="s1">mirtavel</span><span class="s2">plimber</span><span class="s3">trelvanet</span><span class="s4">vendoloop</span>
  </nav>
  <div class="contact-line" style="left:518px">
    <svg width="17" height="17" viewBox="0 0 24 24"><path fill="#e2352b" d="M6.6 10.8a15 15 0 0 0 6.6 6.6l2.2-2.2c.3-.3.7-.4 1-.2 1.1.4 2.3.6 3.6.6.6 0 1 .4 1 1V20c0 .6-.4 1-1 1A17 17 0 0 1 3 4c0-.6.4-1 1-1h3.5c.6 0 1 .4 1 1 0 1.3.2 2.5.6 3.6.1.3 0 .7-.2 1z"/></svg>
    555-014-2290
  </div>
  <div class="contact-line" style="left:657px">
    <svg width="21" height="15" viewBox="0 0 21 15"><rect x="0.5" y="0.5" width="20" height="14" fill="none" stroke="#e2352b" stroke-width="2"/><path d="M1 1l9.5 7L20 1M1 14l7-6M20 14l-7-6" fill="none" stroke="#e2352b" stroke-width="2"/></svg>
    info@kolvarinlink.com
  </div>
  <div class="menu-toggle"><i style="top:7px"></i><i style="top:12px"></i><i style="top:17px"></i></div>
</header>

<section class="hero">
  <div class="hero-floor"></div>
  <div class="lamps" role="img" aria-label="Three pendant lamps hanging from the ceiling"></div>
  <h1 class="hero-title">WE DESIGN &amp; DEVELOP YOUR DREAMS</h1>
  <div class="devices" role="img" aria-label="Phone, tablet, desktop monitor and laptop showing colourful website layouts"></div>
  <a class="btn-contact">CONTACT US</a>
  <div class="dots"><span></span><span class="on"></span><span></span></div>
</section>

<section class="services">
  <article class="card" style="left:78px">
    <div class="card-media" style="border-color:var(--green);background:linear-gradient(135deg,#f6c21a,#f3d94a 50%,#35b9c9)" role="img" aria-label="Designer desk with a monitor and colourful stationery on a yellow wall"></div>
    <h3>CREATIVE DESIGN</h3>
    <p>Ut wisi enim ad minim veniam, quis nostrud exercimli tation ullamcorper suscipit lobortis nisl ut aliquip exm ea commodo consequat.</p>
  </article>
  <article class="card" style="left:348px">
    <div class="card-media" style="border-color:var(--orange);background:linear-gradient(135deg,#4f8ac9,#5b97d2 60%,#3f74b3)" role="img" aria-label="Flat illustration of hands using phones and tablets over a blue background"></div>
    <h3>APP DEVELOPMENT</h3>
    <p>Ut wisi enim ad minim veniam, quis nostrud exercimli tation ullamcorper suscipit lobortis nisl ut aliquip exm ea commodo consequat.</p>
  </article>
  <article class="card" style="left:618px">
    <div class="card-media" style="border-color:var(--red);background:radial-gradient(circle at 52% 65%,#bfe9ff 0%,#2f8fb8 22%,#0c3f5c 60%,#06223a 100%)" role="img" aria-label="Hanging light bulbs in blue light with one bulb glowing"></div>
    <h3>NEW PRODUCT INNOVATION</h3>
    <p>Ut wisi enim ad minim veniam, quis nostrud exercimli tation ullamcorper suscipit lobortis nisl ut aliquip exm ea commodo consequat.</p>
  </article>
</section>

<section class="about">
  <h2><span class="a">ABOUT</span> KOLVARIN <span class="c">LINK</span></h2>
  <div class="divider"><i></i></div>
  <p>Lorem ipsum dolor sit amet, consectetuer adipiscing elit, sed diam nonummy nibh euismod tincidunt ut laoreet dolore magna aliquam erat volutpat. Ut wisi enim ad minim veniam, quis nostrud exerci tation ullamcorper suscipit lobortis nisl ut aliquip ex ea commodo consequat. Duis autem vel eum iriure dolor in hendrerit in vulputate velit esse molestie consequat, vel illum dolore eu feugiat nulla facilisis at vero eros et accumsan et iusto odio dignissim qui blandit praesent luptatum zzril delenit augue duis dolore te feugait nulla facilisi.</p>
</section>

<footer>
  <div class="newsletter-band">
    <svg class="abs" style="left:78px;top:18px" width="22" height="22" viewBox="0 0 22 22"><path d="M1 9l10-7 10 7v12H1z" fill="#fff"/><path d="M1 9l10 7 10-7" fill="none" stroke="#5f9a3c" stroke-width="1.5"/><circle cx="11" cy="9" r="3" fill="none" stroke="#5f9a3c" stroke-width="1.3"/></svg>
    <form class="signup"><input type="text" placeholder="Enter Your Email Here"><button type="button">GO</button></form>
    <div class="footer-brand"><span class="brand-mark"></span><span class="brand-name">KOLVARIN</span></div>
    <div class="follow-group">
      <span class="follow">Follow Us On</span>
      <nav class="social">
        <span class="s1">mirtavel</span><span class="s2">plimber</span><span class="s3">trelvanet</span><span class="s4">vendoloop</span>
      </nav>
    </div>
  </div>
  <div class="info-band">
    <div class="info-row" style="left:148px">
      <svg width="9" height="12" viewBox="0 0 9 12"><path d="M4.5 0A4.5 4.5 0 0 0 0 4.5C0 8 4.5 12 4.5 12S9 8 9 4.5A4.5 4.5 0 0 0 4.5 0z" fill="#fff"/><circle cx="4.5" cy="4.5" r="1.6" fill="#333"/></svg>
      Contrary to popular belief, Lorem Ipsum is.
    </div>
    <div class="info-row" style="left:377px">
      <svg width="11" height="11" viewBox="0 0 24 24"><path fill="#fff" d="M6.6 10.8a15 15 0 0 0 6.6 6.6l2.2-2.2c.3-.3.7-.4 1-.2 1.1.4 2.3.6 3.6.6.6 0 1 .4 1 1V20c0 .6-.4 1-1 1A17 17 0 0 1 3 4c0-.6.4-1 1-1h3.5c.6 0 1 .4 1 1 0 1.3.2 2.5.6 3.6.1.3 0 .7-.2 1z"/></svg>
      Phone: 555-014-2290
    </div>
    <div class="info-row" style="left:520px">
      <svg width="14" height="10" viewBox="0 0 14 10"><rect width="14" height="10" fill="#fff"/><path d="M0 0l7 5 7-5" fill="none" stroke="#333"/></svg>
      Email: info@kolvarinlink.com
    </div>
    <div class="info-row" style="left:697px">
      <svg width="12" height="11" viewBox="0 0 12 11"><rect x="2.5" y="0" width="7" height="3" fill="#fff"/><rect x="0" y="3.5" width="12" height="5" rx="1" fill="#fff"/><rect x="2.5" y="7" width="7" height="4" fill="#fff" stroke="#333" stroke-width=".8"/></svg>
      Fax: 555-014-2290
    </div>
    <div class="copyright">Copyright © 2016 Kolvarin Link. All Rights Reserved.</div>
  </div>
</footer>

</body>
</html>
```